Brightwave Reach - Business Card

We need a business card for a Social Media Marketing company that specializes in online marketing for small businesses in Canada using common Social Media platforms such as Pixlora, Chatterly, Blinkpost & Quibber.

I have uploaded a copy of our logo which I would like utilized in the business card. We would like the business card to be modern yet classy design.

Our website is www.brightwavereach.ca

Industry/Entity Type

Marketing

Contact Information for Business Card

Email: info@brightwavereach.ca
Website: www.brightwavereach.ca
Telephone: 604-555-0193

Colors

Designer to choose colors to be used in the design.

Requirements
Must have
• Social Media icons on reverse
• Please add some designs with color.

```html
<!DOCTYPE html>
<html lang="en">
<head>
<meta charset="utf-8">
<title>Brightwave Reach – Business Card</title>
<link rel="stylesheet" href="https://fonts.googleapis.com/css2?family=Oswald:wght@300;400;700&display=swap">
<style>
  :root {
    --backdrop: #2b1d15;
    --card: #0b0b0b;
    --card-sheen: #222222;
    --ink: #f2f2f2;
    --ink-soft: #cfcfcf;
    --accent-1: #e8453c;
    --accent-2: #f5a623;
    --accent-3: #2bb3a3;
    --accent-4: #3d7be0;
  }
  * { margin: 0; padding: 0; box-sizing: border-box; }
  html, body {
    width: 848px;
    height: 1200px;
    overflow: hidden;
    background: var(--backdrop);
  }
  .sheet {
    width: 848px;
    height: 1200px;
    display: flex;
    flex-direction: column;
    justify-content: space-around;
    align-items: center;
    padding: 60px 0;
  }
  .card {
    width: 560px;
    height: 320px;
    background: linear-gradient(120deg, var(--card) 0%, var(--card-sheen) 50%, var(--card) 100%);
    border-radius: 4px;
    box-shadow: 0 18px 40px rgba(0, 0, 0, 0.55);
    position: relative;
    overflow: hidden;
    color: var(--ink);
    font-family: 'Oswald', sans-serif;
  }
  .accent-bar {
    position: absolute;
    left: 0;
    right: 0;
    bottom: 0;
    height: 6px;
    display: flex;
  }
  .accent-bar span { flex: 1; }
  .accent-bar span:nth-child(1) { background: var(--accent-1); }
  .accent-bar span:nth-child(2) { background: var(--accent-2); }
  .accent-bar span:nth-child(3) { background: var(--accent-3); }
  .accent-bar span:nth-child(4) { background: var(--accent-4); }

  /* Front */
  .brand {
    position: absolute;
    left: 70px;
    top: 50%;
    transform: translateY(-50%);
    display: flex;
    align-items: center;
    gap: 20px;
  }
  .brand__mark {
    width: 24px;
    height: 24px;
    background: var(--ink);
    flex: none;
  }
  .brand__name {
    font-weight: 700;
    font-size: 54px;
    letter-spacing: 1px;
    text-transform: uppercase;
    line-height: 0.95;
    color: var(--ink);
  }
  .front__web {
    position: absolute;
    right: 24px;
    top: 50%;
    transform: translateY(-50%) rotate(-90deg);
    transform-origin: center;
    margin-right: -70px;
    font-weight: 400;
    font-size: 15px;
    letter-spacing: 1px;
    color: var(--ink-soft);
    white-space: nowrap;
  }

  /* Back */
  .card--back {
    padding: 0 48px 46px;
    display: flex;
    flex-direction: column;
    justify-content: flex-end;
    gap: 10px;
  }
  .socials {
    display: flex;
    gap: 22px;
    list-style: none;
    margin-bottom: 16px;
  }
  .social {
    display: flex;
    align-items: center;
    gap: 7px;
    font-weight: 400;
    font-size: 14px;
    letter-spacing: 1px;
    color: var(--ink);
  }
  .social__dot {
    width: 12px;
    height: 12px;
    border-radius: 50%;
  }
  .social:nth-child(1) .social__dot { background: var(--accent-1); }
  .social:nth-child(2) .social__dot { background: var(--accent-2); }
  .social:nth-child(3) .social__dot { background: var(--accent-3); }
  .social:nth-child(4) .social__dot { background: var(--accent-4); }
  .contact {
    font-weight: 300;
    font-size: 18px;
    letter-spacing: 2.5px;
    color: var(--ink);
    white-space: nowrap;
  }
  .contact__divider { margin: 0 8px; }
</style>
</head>
<body>
  <main class="sheet">
    <section class="card card--front" aria-label="Card front">
      <div class="brand">
        <span class="brand__mark"></span>
        <span class="brand__name">Brightwave<br>Reach</span>
      </div>
      <p class="front__web">www.brightwavereach.ca</p>
      <div class="accent-bar"><span></span><span></span><span></span><span></span></div>
    </section>

    <section class="card card--back" aria-label="Card back">
      <ul class="socials">
        <li class="social"><span class="social__dot"></span>Pixlora</li>
        <li class="social"><span class="social__dot"></span>Chatterly</li>
        <li class="social"><span class="social__dot"></span>Blinkpost</li>
        <li class="social"><span class="social__dot"></span>Quibber</li>
      </ul>
      <p class="contact">604-555-0193<span class="contact__divider">|</span>info@brightwavereach.ca</p>
      <p class="contact">www.brightwavereach.ca</p>
      <div class="accent-bar"><span></span><span></span><span></span><span></span></div>
    </section>
  </main>
</body>
</html>
```